"Tandem Mouthguards " Custom-made Mouthguard Business Website

We need an informational website for our mouthguard Business "Tandem Mouthguards". The logo is navy blue/lime green so want to have colour scheme that goes nicely with this - have uploaded our mouthguard flyer with some information we need to put into the website but I do have more information to put in there.

Target Market(s)

Sports clubs, sportspeople, parents and kids, schools

Industry/Entity Type

Dental, Custom-made Sports Mouthguards

Coding

Coded - Design and coding required

Number of Pages Required

5+ page

Font styles to use
Serif
Sans Serif

Colors
0054AA
0677BA
7BADD7
CADEEF
E8F1F8
0094D4
00A9DD
6FCCEA
C7EBF8
E9F6FB
00AB8E
00BBA5
67D7C9
C6EFE9
E9F9F6
59FF00
82FF00
B8FF75
E3FFCB
F4FFEA
FFF300
FFF600
FEFA6F
FFFEC7
FFFEE8
FFC000
F8CF3A
FAE287
FDF2CF
FEFAEE
F0912C
F2A743
F7CA91
FBE8D2
FDF5EE
EE7325
F08F49
F5BC92
FAE3D3
FDF4ED

Requirements
Must have
• I want drop down pages, not one scrolling page. Different pages for each heading . Content uploaded - We need a general home page with lots of pictures and info that I'll provide. A page each dedicated to 1) About Us 2) Why choose a custom mouthguard? 3) Gallery 4) Contact Us. Will need logos from "Velora"
Nice to have
• Mainly use greens and blues, but happy to pop in some yellow/oranges/red oranges if it looks good

```html
<!DOCTYPE html>
<html lang="en">
<head>
<meta charset="UTF-8">
<title>Tandem Mouthguards</title>
<link href="https://fonts.googleapis.com/css2?family=Montserrat:wght@400;500;600;700;800;900&family=Open+Sans:wght@400;600&display=swap" rel="stylesheet">
<style>
:root{
  --navy:#0c2a5c;
  --navy-deep:#0a2350;
  --green:#3cc22c;
  --green-bright:#59d21a;
  --orange:#f07a1e;
  --pale:#e8f1f8;
  --text:#1c2b45;
  --muted:#4a5870;
  --white:#ffffff;
}
*{margin:0;padding:0;box-sizing:border-box}
html,body{width:1200px;height:4184px;overflow:hidden;background:var(--white)}
body{font-family:"Open Sans",Arial,sans-serif;color:var(--text)}
.page{position:relative;width:1200px;height:4184px;overflow:hidden}
.abs{position:absolute}
h1,h2,h3,.nav,.btn,.brand{font-family:"Montserrat",Arial,sans-serif}

/* header */
.site-header{left:0;top:0;width:1200px;height:92px;background:var(--white)}
.brand{position:absolute;left:120px;top:18px;line-height:1;color:var(--navy);font-weight:900}
.brand .b1{display:block;font-size:34px;letter-spacing:1px}
.brand .b2{display:block;font-size:15px;letter-spacing:2.4px;margin-top:3px}
.nav{position:absolute;right:110px;top:30px;display:flex;gap:34px;font-size:14px;font-weight:700;color:var(--navy)}
.nav span{position:relative;padding-bottom:8px}
.nav .active{color:var(--green)}
.nav .active::after{content:"";position:absolute;left:0;right:0;bottom:0;height:3px;background:var(--green)}

/* hero */
.hero{left:0;top:92px;width:1200px;height:650px;
  background:
    radial-gradient(ellipse 170px 130px at 790px 360px,rgba(240,200,30,.85),rgba(240,200,30,0)),
    radial-gradient(ellipse 220px 260px at 640px 470px,rgba(110,60,160,.75),rgba(110,60,160,0)),
    radial-gradient(ellipse 230px 280px at 1000px 460px,rgba(40,70,150,.9),rgba(40,70,150,0)),
    radial-gradient(ellipse 150px 150px at 620px 230px,rgba(222,170,140,.55),rgba(222,170,140,0)),
    radial-gradient(ellipse 150px 150px at 960px 210px,rgba(222,170,140,.5),rgba(222,170,140,0)),
    radial-gradient(ellipse 380px 300px at 1100px 80px,rgba(90,130,70,.7),rgba(90,130,70,0)),
    linear-gradient(90deg,#08214a 0%,#123a78 40%,#2f5f98 65%,#3d6b6a 100%)}
.hero-shade{left:0;top:92px;width:640px;height:650px;background:linear-gradient(90deg,rgba(5,20,50,.75),rgba(5,20,50,0))}
.hero-title{left:120px;top:272px;color:var(--white);font-size:40px;font-weight:600;line-height:1.18;letter-spacing:.5px}
.hero-title strong{font-weight:800;display:block}
.btn{display:inline-block;border-radius:30px;font-size:14px;font-weight:800;color:var(--white);text-align:center;letter-spacing:.5px}
.btn-green{background:var(--green)}
.btn-orange{background:var(--orange)}
.hero-btn{left:120px;top:430px;width:154px;height:46px;line-height:46px}

/* why choose */
.section-title{left:0;width:1200px;text-align:center;color:var(--navy);font-size:40px;font-weight:500;letter-spacing:1px}
.section-title b{font-weight:800}
.title-rule{width:90px;height:4px;background:var(--green);left:555px}
.card{width:300px;height:222px;border:2px solid #1e3d72;border-radius:14px;background:var(--white);text-align:center;padding:78px 22px 0;font-size:19px;font-weight:600;color:var(--navy);line-height:1.3}
.card.featured{background:var(--navy);color:var(--white);font-weight:500}
.card-icon{position:absolute;left:50%;top:-40px;margin-left:-44px;width:88px;height:88px;border-radius:50%;background:var(--green);display:flex;align-items:center;justify-content:center}
.gap-free{left:0;width:1200px;top:1492px;text-align:center;font-family:"Montserrat",Arial,sans-serif;font-weight:800;font-size:21px;color:var(--navy);line-height:1.35}

/* about */
.about{left:0;top:1600px;width:1200px;height:580px;background:var(--pale)}
.photo{border-radius:6px}
.about-title{left:652px;top:1704px;color:var(--navy);font-size:36px;line-height:1.1;font-weight:500}
.about-title b{font-weight:800;display:block}
.about-rule{left:652px;top:1794px;width:80px;height:4px;background:var(--green)}
.about-copy{left:652px;top:1818px;width:440px;font-size:16px;line-height:1.5;color:var(--muted)}
.about-copy p+p{margin-top:18px}
.about-btn{left:652px;top:2086px;width:190px;height:48px;line-height:48px}

/* personalise */
.personalise{left:0;top:2248px;width:1200px;height:624px;background:var(--navy-deep)}
.pers-title{left:120px;top:2378px;color:var(--white);font-size:34px;font-weight:500;letter-spacing:.5px}
.pers-title b{font-weight:800}
.pers-rule{left:120px;top:2430px;width:80px;height:4px;background:var(--green)}
.pers-copy{left:120px;top:2452px;width:470px;color:#dfe8f5;font-size:17px;line-height:1.5}
.pers-list{left:120px;top:2520px;list-style:none;color:#dfe8f5;font-size:17px;line-height:2}
.pers-list li::before{content:"";display:inline-block;width:9px;height:9px;border-radius:50%;background:var(--green);margin-right:16px;vertical-align:middle}
.pers-btn{left:120px;top:2682px;width:196px;height:52px;line-height:52px}
.pers-art{left:640px;top:2330px;width:500px;height:500px;border-radius:50%;
  background:
    radial-gradient(ellipse 120px 80px at 190px 250px,rgba(245,245,245,.9),rgba(245,245,245,0)),
    radial-gradient(ellipse 110px 70px at 320px 240px,rgba(40,90,190,.9),rgba(40,90,190,0)),
    linear-gradient(135deg,#3f78c8 0%,#2a5fb0 42%,#f2c81a 52%,#f7d64a 58%,#2c5ea8 70%,#1f4a8e 100%)}

/* gallery */
.gallery-btn{left:520px;top:3562px;width:160px;height:52px;line-height:52px}

/* booking + footer */
.footer-band{left:0;top:3830px;width:1200px;height:254px;background:var(--pale)}
.booking{left:88px;top:3692px;width:1044px;height:248px;background:var(--green-bright);border-radius:10px;text-align:center}
.booking h2{margin-top:40px;font-size:40px;font-weight:500;color:var(--navy);letter-spacing:.5px}
.booking h2 b{font-weight:800}
.booking p{margin-top:12px;font-family:"Montserrat",Arial,sans-serif;font-weight:600;font-size:16px;color:var(--navy)}
.booking .actions{margin-top:26px;display:flex;justify-content:center;gap:16px}
.btn-white{background:var(--white);color:var(--navy);width:172px;height:50px;line-height:50px}
.btn-navy{background:var(--navy);width:212px;height:50px;line-height:50px;display:flex;align-items:center;justify-content:center;gap:10px}
.foot-brand{left:120px;top:3972px}
.foot-brand .b1{font-size:30px}
.foot-brand .b2{font-size:13px}
.foot-nav{position:absolute;left:384px;top:4004px;display:flex;gap:40px;font-size:14px;font-weight:700;color:var(--navy)}
.copyright{left:120px;top:4124px;font-size:14px;color:var(--muted)}
.partner{left:736px;top:4108px;display:flex;align-items:center;gap:10px;font-family:"Montserrat",Arial,sans-serif;font-weight:700;font-size:17px;color:#2a8fd0}
.partner i{width:26px;height:26px;border-radius:50%;background:#2a8fd0;display:block}
.socials{left:998px;top:4112px;display:flex;gap:10px}
.socials span{width:30px;height:30px;border-radius:50%;background:var(--green);display:block}
.socials span:nth-child(2){background:var(--navy)}
</style>
</head>
<body>
<div class="page">

  <header class="abs site-header">
    <div class="brand"><span class="b1">TANDEM</span><span class="b2">MOUTHGUARDS</span></div>
    <nav class="nav">
      <span class="active">HOME</span>
      <span>ABOUT</span>
      <span>WHY CHOOSE A CUSTOM MOUTHGUARD?</span>
      <span>GALLERY</span>
      <span>CONTACT US</span>
    </nav>
  </header>

  <div class="abs hero" role="img" aria-label="Two smiling children in football club guernseys holding a yellow football, wearing coloured custom mouthguards"></div>
  <div class="abs hero-shade"></div>
  <h1 class="abs hero-title">PROTECT YOUR SMILE<strong>WITH A COMFORTABLE,</strong><strong>PROFESSIONAL FIT.</strong></h1>
  <span class="abs btn btn-green hero-btn">BOOK NOW</span>

  <h2 class="abs section-title" style="top:800px">WHY <b>CHOOSE US</b></h2>
  <div class="abs title-rule" style="top:862px"></div>

  <div class="abs card" style="left:132px;top:940px">
    <div class="card-icon"><svg width="46" height="46" viewBox="0 0 46 46" fill="none" stroke="#fff" stroke-width="2.5"><circle cx="23" cy="14" r="8"/><path d="M8 42c0-9 7-15 15-15s15 6 15 15"/><path d="M19 34h8M23 30v8"/></svg></div>
    Professionally made by a qualified dental prosthetist
  </div>
  <div class="abs card featured" style="left:450px;top:940px">
    <div class="card-icon"><svg width="46" height="46" viewBox="0 0 46 46" fill="none" stroke="#fff" stroke-width="2.5"><path d="M10 8v14a13 13 0 0 0 26 0V8"/><path d="M17 8v14a6 6 0 0 0 12 0V8"/></svg></div>
    Custom fit for comfort, protection, and durability
    <svg style="display:block;margin:18px auto 0" width="14" height="14"><circle cx="7" cy="7" r="6" fill="#fff"/></svg>
  </div>
  <div class="abs card" style="left:768px;top:940px">
    <div class="card-icon"><svg width="46" height="46" viewBox="0 0 46 46" fill="none" stroke="#fff" stroke-width="2.5"><path d="M23 6a17 17 0 1 0 0 34c3 0 4-2 3-4s0-5 3-5h5c4 0 6-3 6-7C40 14 32 6 23 6z"/><circle cx="15" cy="20" r="2.5"/><circle cx="22" cy="13" r="2.5"/><circle cx="30" cy="16" r="2.5"/></svg></div>
    Wide range of colours and designs
  </div>
  <div class="abs card" style="left:296px;top:1218px">
    <div class="card-icon"><svg width="50" height="46" viewBox="0 0 50 46" fill="none" stroke="#fff" stroke-width="2.5"><circle cx="14" cy="14" r="6"/><circle cx="36" cy="14" r="6"/><circle cx="25" cy="22" r="5"/><path d="M3 40c0-8 5-13 11-13M47 40c0-8-5-13-11-13M15 42c0-7 4-11 10-11s10 4 10 11"/></svg></div>
    Available for kids, teens, and adults
  </div>
  <div class="abs card" style="left:614px;top:1218px">
    <div class="card-icon"><svg width="46" height="46" viewBox="0 0 46 46" fill="none" stroke="#fff" stroke-width="2.5"><path d="M6 40V18l17-10 17 10v22z"/><path d="M18 40V28h10v12"/><path d="M16 20h4M26 20h4"/></svg></div>
    Clinic and mobile school/club visits available
  </div>

  <p class="abs gap-free" style="top:1494px">TALK TO US ABOUT OUR "GAP FREE" MOUTHGUARDS FOR ELIGIBLE<br>PRIVATE HEALTH INSURANCE MEMBERS.</p>

  <section class="abs about"></section>
  <div class="abs photo" style="left:120px;top:1680px;width:232px;height:224px;background:radial-gradient(ellipse at 50% 50%,#7fb04a,#3f7a38 60%,#2c5a2c)" role="img" aria-label="Green custom mouthguard"></div>
  <div class="abs photo" style="left:120px;top:1920px;width:232px;height:232px;background:radial-gradient(ellipse at 50% 55%,#5a8fd0,#2b5fa8 55%,#1a3558)" role="img" aria-label="Blue marbled mouthguard"></div>
  <div class="abs photo" style="left:368px;top:1788px;width:232px;height:224px;background:radial-gradient(ellipse at 45% 50%,#9a6ad0,#5e3496 55%,#2e1e40)" role="img" aria-label="Purple glitter mouthguard held in hand"></div>
  <h2 class="abs about-title">ABOUT <b>TANDEM MOUTHGUARDS</b></h2>
  <div class="abs about-rule"></div>
  <div class="abs about-copy">
    <p>With over 20 years experience in the industry, our dental prosthetists take care to provide mouth-guards that are made with precision and shaped for your comfort and protection.</p>
    <p>We are pleased to provide "gap free" mouthguards to all private health fund members with dental coverage, meaning you won't have any out of pocket expenses.</p>
  </div>
  <span class="abs btn btn-orange about-btn">BOOK NOW</span>

  <section class="abs personalise"></section>
  <h2 class="abs pers-title">PERSONALISE <b>YOUR STYLE</b></h2>
  <div class="abs pers-rule"></div>
  <p class="abs pers-copy">Stand out on the field with your choice of colours, patterns, and style combinations:</p>
  <ul class="abs pers-list">
    <li>Team colours</li>
    <li>Marbled, striped, and chequered patterns</li>
    <li>Clear or solid shades</li>
    <li>Add your name or player number</li>
  </ul>
  <span class="abs btn btn-orange pers-btn">BOOK NOW</span>
  <div class="abs pers-art" role="img" aria-label="Illustration of blue, white and yellow team colour mouthguards on a striped round backdrop"></div>

  <h2 class="abs section-title" style="top:2966px">PHOTO <b>GALLERY</b></h2>
  <div class="abs title-rule" style="top:3028px"></div>
  <div class="abs photo" style="left:88px;top:3052px;width:344px;height:328px;background:radial-gradient(circle at 50% 50%,#4f8ad0,#2a5ea4 50%,#6b5a48 75%,#8a7a62)" role="img" aria-label="Blue speckled mouthguard on a table"></div>
  <div class="abs photo" style="left:88px;top:3392px;width:344px;height:128px;background:linear-gradient(135deg,#2e62a8,#5b8fcf 60%,#8a7a62)" role="img" aria-label="Blue marbled mouthguard"></div>
  <div class="abs photo" style="left:448px;top:3052px;width:340px;height:226px;background:radial-gradient(ellipse at 50% 50%,#6f8a3a,#8c8a4e 50%,#5a5a2c)" role="img" aria-label="Green and gold mouthguard in case"></div>
  <div class="abs photo" style="left:448px;top:3290px;width:340px;height:230px;background:radial-gradient(ellipse at 50% 50%,#7a4ab0,#6a5a3e 60%,#4a3a2a)" role="img" aria-label="Purple mouthguard on a tray"></div>
  <div class="abs photo" style="left:800px;top:3052px;width:340px;height:468px;background:radial-gradient(ellipse at 50% 62%,#a02a3e,#8a2b3b 25%,#e4e4e4 50%,#c8c8c8 80%,#9a9a9a)" role="img" aria-label="Maroon named mouthguard in a white case"></div>
  <span class="abs btn btn-orange gallery-btn">VIEW MORE</span>

  <div class="abs footer-band"></div>
  <div class="abs booking">
    <h2>MAKE A <b>BOOKING NOW</b></h2>
    <p>PLEASE CONTACT US TO MAKE A BOOKING FOR YOUR NEW CUSTOM MOUTHGUARD</p>
    <div class="actions">
      <span class="btn btn-white">CONTACT US</span>
      <span class="btn btn-navy"><svg width="22" height="22" viewBox="0 0 22 22"><circle cx="11" cy="11" r="11" fill="#fff"/><path d="M7 5.5l2.2 2.6-1.2 1.4a8 8 0 0 0 4.5 4.5l1.4-1.2 2.6 2.2-1.3 1.8c-5 0-10-5-10-10z" fill="#0c2a5c"/></svg>(08) 5550 1234</span>
    </div>
  </div>

  <div class="brand abs foot-brand"><span class="b1">TANDEM</span><span class="b2">MOUTHGUARDS</span></div>
  <nav class="foot-nav">
    <span>ABOUT</span><span>WHY CHOOSE A CUSTOM MOUTHGUARD</span><span>GALLERY</span><span>FAQS</span><span>CONTACT US</span>
  </nav>

  <p class="abs copyright">© 2025 Company Name | All Rights Reserved</p>
  <div class="abs partner"><i></i>Harbour Denture Care</div>
  <div class="abs socials"><span></span><span></span><span></span></div>

</div>
</body>
</html>
```